Single-sided business card for restaurant velmora with new logo made on this site

Business card options with new logo including restaurant name, address, phone number and website. This business card is single-sided only and will be presented at the hostess desk for clients to take. I would like to see options based on a cream card background, a white card background, a yellow card background and a burgundy colored background. It needs to be elegant and traditional.

Target Market(s)

local and international crowd

Industry/Entity Type

restaurant

Contact Information for Business Card

address, website and phone number

Font styles to use
Serif

Colors
EE7325
F08F49
F5BC92
FAE3D3
FDF4ED

Requirements
Must have
• new logo, address, phone number, website
Should not have
• more than three colors

```html
<!DOCTYPE html>
<html lang="es">
<head>
<meta charset="utf-8">
<title>Velmora – Tarjeta de presentación</title>
<link href="https://fonts.googleapis.com/css2?family=Cinzel:wght@400;500;600&display=swap" rel="stylesheet">
<style>
  :root {
    --backdrop: #6e5238;
    --card: #fbfbfa;
    --ink: #3a1c16;
    --gold: #f0ae2c;
  }
  * { margin: 0; padding: 0; box-sizing: border-box; }
  html, body {
    width: 900px; height: 1200px; overflow: hidden;
    background: var(--backdrop);
  }
  .canvas { position: relative; width: 900px; height: 1200px; }

  .card {
    position: absolute; left: 73px; width: 777px; height: 459px;
    background: var(--card);
    box-shadow: 0 2px 8px rgba(0,0,0,.25);
    font-family: "Cinzel", "Times New Roman", serif;
    color: var(--ink);
  }
  .card--stacked-rules { top: 127px; }
  .card--compact { top: 618px; }

  .brand {
    position: absolute; left: 95px; width: 190px;
    display: flex; flex-direction: column; align-items: center;
  }
  .brand__square { width: 112px; height: 112px; background: var(--gold); }
  .brand__name {
    margin-top: 20px;
    font-size: 38px; font-weight: 500; letter-spacing: 5px;
    line-height: 1; color: var(--ink);
  }
  .card--stacked-rules .brand { top: 131px; }
  .card--compact .brand { top: 131px; }

  .divider {
    position: absolute; left: 367px; width: 2px; background: var(--gold);
  }
  .card--stacked-rules .divider { top: 75px; height: 310px; }
  .card--compact .divider { top: 94px; height: 272px; }

  .details { position: absolute; left: 428px; }
  .card--stacked-rules .details { top: 80px; }
  .card--compact .details { top: 94px; }

  .details__line {
    font-size: 21px; font-weight: 500; line-height: 31.5px;
    letter-spacing: .3px; white-space: nowrap;
  }
  .rule {
    width: 93px; height: 2px; background: var(--gold);
    margin: 17px 0 18px;
  }
</style>
</head>
<body>
<main class="canvas">

  <section class="card card--stacked-rules" aria-label="Tarjeta, versión con separadores">
    <div class="brand">
      <div class="brand__square"></div>
      <div class="brand__name">VELMORA</div>
    </div>
    <div class="divider"></div>
    <div class="details">
      <p class="details__line">Restaurant Velmora</p>
      <div class="rule"></div>
      <p class="details__line">Jacaranda 415</p>
      <p class="details__line">Bahías de Huatulco,</p>
      <p class="details__line">Oaxaca CP 70912</p>
      <div class="rule"></div>
      <p class="details__line">Reservaciones</p>
      <p class="details__line">958-555-0142</p>
      <p class="details__line">www.velmora.com.mx</p>
    </div>
  </section>

  <section class="card card--compact" aria-label="Tarjeta, versión compacta">
    <div class="brand">
      <div class="brand__square"></div>
      <div class="brand__name">VELMORA</div>
    </div>
    <div class="divider"></div>
    <div class="details">
      <p class="details__line">Restaurant Velmora</p>
      <p class="details__line">Jacaranda 415</p>
      <p class="details__line">Bahías de Huatulco,</p>
      <p class="details__line">Oaxaca CP 70912</p>
      <div class="rule"></div>
      <p class="details__line">Reservaciones</p>
      <p class="details__line">958-555-0142</p>
      <p class="details__line">www.velmora.com.mx</p>
    </div>
  </section>

</main>
</body>
</html>
```